Verodex business card

Business card for sustainable investment company called "Verodex". Verodex is an exchange platform selling carbon credits between buyers and sellers. Carbon Credits are an environmental commodity for reducing global carbon emissions.

the card should obviously have our logo and the theme should be sustainability/environment mixed with a trading platform.

Contact Information for Business Card

Logo, Name, Title, Phone, Email

Colors
0054AA
0677BA
7BADD7
CADEEF
E8F1F8
0094D4
00A9DD
6FCCEA
C7EBF8
E9F6FB
00AB8E
00BBA5
67D7C9
C6EFE9
E9F9F6
59FF00
82FF00
B8FF75
E3FFCB
F4FFEA

```html
<!DOCTYPE html>
<html lang="en">
<head>
<meta charset="UTF-8">
<title>Verodex Business Card</title>
<link rel="stylesheet" href="https://fonts.googleapis.com/css2?family=Montserrat:wght@700&family=Open+Sans:wght@400;600;700&display=swap">
<style>
  :root {
    --page: #e6e8ec;
    --card: #1e1e23;
    --white: #ffffff;
    --muted: #d9dde3;
    --blue-deep: #0677ba;
    --blue: #4a7fd0;
    --cyan: #6fcce6;
    --shadow: rgba(10, 12, 20, 0.28);
  }
  * { box-sizing: border-box; margin: 0; padding: 0; }
  html, body { width: 1200px; height: 780px; overflow: hidden; }
  body {
    background: var(--page);
    font-family: "Open Sans", Arial, sans-serif;
    position: relative;
  }
  .card {
    position: absolute;
    width: 540px;
    height: 310px;
    background: var(--card);
    border-radius: 22px;
    overflow: hidden;
    box-shadow: 0 18px 40px var(--shadow);
    top: 235px;
  }
  .card--front { left: 40px; border-bottom: 4px solid var(--cyan); }
  .card--back { left: 620px; }

  .wordmark {
    display: flex;
    align-items: center;
    gap: 12px;
    font-family: "Montserrat", Arial, sans-serif;
    font-weight: 700;
    color: var(--white);
    letter-spacing: 0.02em;
  }
  .wordmark__dot {
    background: var(--blue);
    border-radius: 4px;
  }
  .card--front .wordmark {
    position: absolute;
    left: 50%; top: 50%;
    transform: translate(-50%, -50%);
    font-size: 52px;
  }
  .card--front .wordmark__dot { width: 46px; height: 46px; }

  .card__bands { position: absolute; inset: 0; }

  .card--back .wordmark {
    position: absolute;
    left: 30px; top: 34px;
    font-size: 30px;
    gap: 10px;
  }
  .card--back .wordmark__dot { width: 28px; height: 28px; border-radius: 3px; }

  .holder {
    position: absolute;
    left: 30px; top: 110px;
    padding-left: 14px;
    border-left: 6px solid var(--blue);
  }
  .holder__name {
    font-size: 27px;
    font-weight: 700;
    color: var(--white);
    line-height: 1.1;
    white-space: nowrap;
  }
  .holder__first { color: var(--blue); }
  .holder__title {
    font-size: 14px;
    color: var(--muted);
    margin-top: 4px;
  }
  .rule {
    position: absolute;
    left: 290px; right: 0; top: 128px;
    height: 2px;
    background: var(--white);
  }

  .contacts {
    position: absolute;
    left: 42px; top: 185px;
    list-style: none;
    font-size: 14px;
    color: var(--white);
  }
  .contacts li { display: flex; align-items: center; gap: 10px; height: 23px; }
  .contacts svg { width: 14px; height: 14px; }

  .address {
    position: absolute;
    right: 28px; top: 150px;
    text-align: right;
    font-size: 13px;
    line-height: 1.45;
    color: var(--white);
  }
</style>
</head>
<body>

  <section class="card card--front" aria-label="Card front">
    <div class="wordmark"><span class="wordmark__dot"></span>VERODEX</div>
  </section>

  <section class="card card--back" aria-label="Card back">
    <svg class="card__bands" viewBox="0 0 540 310" preserveAspectRatio="none" aria-hidden="true">
      <defs>
        <linearGradient id="band-gradient" x1="0" y1="0" x2="1" y2="0">
          <stop offset="0" stop-color="#4a7fd0"/>
          <stop offset="1" stop-color="#6fcce6"/>
        </linearGradient>
      </defs>
      <polygon points="0,278 360,278 372,268 540,268 540,310 0,310" fill="url(#band-gradient)"/>
      <polygon points="0,284 362,284 350,310 0,310" fill="#ffffff"/>
      <polygon points="390,236 540,236 540,268 372,268" fill="url(#band-gradient)"/>
    </svg>

    <div class="wordmark"><span class="wordmark__dot"></span>VERODEX</div>

    <div class="holder">
      <p class="holder__name"><span class="holder__first">Marta</span> Kolinova</p>
      <p class="holder__title">Managing Director</p>
    </div>
    <div class="rule"></div>

    <ul class="contacts">
      <li>
        <svg viewBox="0 0 16 16" aria-hidden="true"><path d="M4 1l3 3-2 2c1 2 3 4 5 5l2-2 3 3-2 3C7 15 1 9 1 3z" fill="#4a7fd0"/></svg>
        (555) 014-2290
      </li>
      <li>
        <svg viewBox="0 0 16 16" aria-hidden="true"><rect x="1" y="3" width="14" height="10" rx="1" fill="none" stroke="#4a7fd0" stroke-width="1.6"/><path d="M1.5 4l6.5 5 6.5-5" fill="none" stroke="#4a7fd0" stroke-width="1.6"/></svg>
        hello@verodex.co
      </li>
      <li>
        <svg viewBox="0 0 16 16" aria-hidden="true"><circle cx="8" cy="8" r="6.5" fill="none" stroke="#4a7fd0" stroke-width="1.6"/><path d="M1.5 8h13M8 1.5c-3 3.5-3 9.5 0 13M8 1.5c3 3.5 3 9.5 0 13" fill="none" stroke="#4a7fd0" stroke-width="1.3"/></svg>
        www.verodex.co
      </li>
    </ul>

    <p class="address">410 Meadowlark Ave. Suite<br>120 Lakeside, TX 75010</p>
  </section>

</body>
</html>
```